Deisgn A Manual Cover for an Australian Health Training Company

We are looking for an A4 Front of Manual Cover Design for a comprehensive administrative training manual to be launched soon in Australia.

The title of the book is :

"Drafting, Shaping and Shipping Office Paperwork"

for the Australian Medical Office (smaller font)

Written and compiled by Mel Dobrik

Target Market(s)

25-45 year old medical administrative students (usually female)

Industry/Entity Type

It Company

Font styles to use
Serif

Colors
3176b5
f68d4c
33b8a4
fffbf0

Requirements
Must have
• University like perhaps
• Human element (picture/s of people)
• About the concept of designing and producing documents in a health setting (this can be entirely conceptual).
• Conceptual design would be considered
• Appealing

```html
<!DOCTYPE html>
<html lang="en">
<head>
<meta charset="utf-8">
<title>Drafting, Shaping and Shipping Office Paperwork — Manual Cover</title>
<link rel="stylesheet" href="https://fonts.googleapis.com/css2?family=Cinzel:wght@400;500&family=EB+Garamond:wght@400&display=swap">
<style>
  :root {
    --page-bg: #ffffff;
    --cover-bg: #ffffff;
    --ink-navy: #1e2b5f;
    --accent-red: #d0243a;
    --rule-red: #d7334a;
    --edge: #e3e3e3;
    --team-teal: #7cc7b8;
    --team-blue: #5b86c6;
    --team-pink: #e98aa6;
    --team-white: #eef1f4;
  }
  * { margin: 0; padding: 0; box-sizing: border-box; }
  html, body {
    width: 1200px; height: 927px; overflow: hidden;
    background: var(--page-bg);
  }
  .canvas {
    position: relative; width: 1200px; height: 927px;
  }
  .cover {
    position: absolute; left: 320px; top: 96px;
    width: 560px; height: 735px;
    background: var(--cover-bg);
    border: 1px solid var(--edge);
    text-align: center;
  }
  .cover-title {
    position: absolute; left: 0; right: 0; top: 26px;
    font-family: "Cinzel", "Times New Roman", serif;
    font-weight: 400;
    font-size: 35px; line-height: 40px;
    letter-spacing: 0.5px;
    color: var(--ink-navy);
    text-transform: uppercase;
  }
  .cover-subtitle {
    position: absolute; left: 22px; right: 22px; top: 158px;
    display: flex; align-items: center; gap: 10px;
    font-family: "EB Garamond", "Times New Roman", serif;
    font-size: 19px; color: var(--ink-navy);
    white-space: nowrap;
  }
  .cover-subtitle .rule-left { flex: 0 0 112px; height: 1px; background: var(--rule-red); }
  .cover-subtitle .rule-right { flex: 1; height: 1px; background: var(--rule-red); }
  .cover-subtitle .rule-left, .cover-subtitle .rule-right { transform: translateY(-10px); }
  .institute {
    position: absolute; left: 0; right: 0; top: 205px;
    display: flex; flex-direction: column; align-items: center; gap: 8px;
  }
  .institute-name {
    font-family: "Cinzel", "Times New Roman", serif;
    font-size: 11px; line-height: 13px; letter-spacing: 0.5px;
    color: var(--ink-navy);
  }
  .institute-mark {
    width: 44px; height: 44px;
    background: var(--ink-navy);
  }
  .team-photo {
    position: absolute; left: 82px; top: 322px;
    width: 396px; height: 300px;
    border-radius: 40% 40% 6% 6% / 28% 28% 4% 4%;
    background:
      linear-gradient(90deg,
        var(--team-teal) 0%, var(--team-blue) 18%, var(--team-pink) 32%,
        var(--team-blue) 45%, var(--team-teal) 58%, var(--team-pink) 68%,
        var(--team-white) 78%, var(--team-blue) 92%, var(--team-teal) 100%);
    opacity: 0.55;
  }
  .credit-label {
    position: absolute; left: 0; right: 0; top: 628px;
    font-family: "Cinzel", "Times New Roman", serif;
    font-size: 25px; color: var(--accent-red);
  }
  .author-name {
    position: absolute; left: 0; right: 0; top: 662px;
    font-family: "Cinzel", "Times New Roman", serif;
    font-size: 46px; line-height: 52px; letter-spacing: 1px;
    color: var(--accent-red);
    text-transform: uppercase;
  }
</style>
</head>
<body>
<div class="canvas">
  <section class="cover">
    <h1 class="cover-title">Drafting, Shaping<br>and Shipping<br>Office Paperwork</h1>
    <p class="cover-subtitle">
      <span class="rule-left"></span>
      <span class="subtitle-text">for the Australian Medical Office</span>
      <span class="rule-right"></span>
    </p>
    <div class="institute">
      <span class="institute-name">Harbourline Institute<br>of Training</span>
      <span class="institute-mark"></span>
    </div>
    <div class="team-photo" role="img" aria-label="Photograph of a group of smiling medical staff in coloured scrubs and white coats standing together"></div>
    <p class="credit-label">Written &amp; Compiled by</p>
    <p class="author-name">Mel Dobrik</p>
  </section>
</div>
</body>
</html>
```